HAIR EXTENSIONS

We need a web design for a company base in Chicago called Tresses by Jolavie. We sale 100% human hair in Brazilian body wave deep wave straight or natural curl, Peruvian body wave straight or deep wave. Malaysian loose straight or body wave, in the chicago land.
We also ship hair to any city or country. We like to see design that use the colors pinks & grays, or would just like to see some design creative with colors thats inviting.

Also I'm using the quillmoss template, Home- banner contact us, about us, Features- product side/left sidebar, Shop- wish list /shopping cart/ tracking your order / checkout/ order received.
Porfolio-filterable 4column portfolio
Blog. Buy now

Industry/Entity Type

Hair

Number of Pages Required

4 page

Colors
aaaaaa
606060
dddddd
eea4c8
d3a5cc
b868aa
a6459a
ffc213
1b1b1b

Requirements
Must have
• I NEED THE DESIGNER TO DO THE 4 PAGE LIKE THIS.
• 1.HOME-PAGE BANNER CONTACT US SOME PRODUCT WITH SIDING IMAGES OF THE TOP PROUDCT
• 2.PRODUCT WITH SHOPPING CART- I WANT SIDING BARS FOR PRODUCT & SHOPPING CART WITH TRACKING YOUR ORDERS CHECK OUT & ORDER RECEIVED.
• 3.PORFOLIO PHOTO-I WANT A FEATURES FOR CUSTOMERS TO UPLOAN THERE PICTURE & BLOG ON THE PAGE
• 4.ABOUT US- TALK ABOUT ARE COMPAMY.
Nice to have
• hello designer
• I was working with a web developer for my site be for i came to craftnookly & they build a site for me that i liked, You all can view it at www.Tressesbyjolavie.info
• long story short never could get them to finish the project after they got paid!!
• I know, why paid before its finish bad decision. So know I'm here starting over with you all.
• here is a list of my competition site
• www.lockswellhub.com
• www.vanoraloft.com
• www.pellinoshop.com
• So just to give some insight, I'm looking for something like the one i had builded.

```html
<!DOCTYPE html>
<html lang="en">
<head>
<meta charset="utf-8">
<title>Tresses by Jolavie — Home</title>
<link rel="stylesheet" href="https://fonts.googleapis.com/css2?family=Oswald:wght@300;400;500&family=Open+Sans:wght@400;600&display=swap">
<style>
:root{
  --ink:#1b1b1b;
  --text:#333333;
  --muted:#606060;
  --line:#cfcfcf;
  --frame:#aaaaaa;
  --red:#a51d24;
  --band-red:#d9464a;
  --navy:#1d2c38;
  --band-grey:#ececec;
  --tag-red:#b3151b;
  --white:#ffffff;
}
*{box-sizing:border-box;margin:0;padding:0}
html,body{width:1200px;height:2281px;overflow:hidden;background:var(--white)}
body{position:relative;font-family:"Open Sans",sans-serif;color:var(--text)}
.abs{position:absolute}

/* header */
.site-header{left:132px;top:43px;width:934px;height:212px;border:2px solid var(--ink)}
.site-header__inner{position:absolute;left:7px;top:7px;right:7px;bottom:7px;border:1px solid var(--frame)}
.contact-line{font-family:"Oswald",sans-serif;font-weight:300;font-size:11px;color:var(--ink);left:20px}
.account-btn{right:16px;top:14px;width:102px;height:25px;border:1px solid var(--muted);font-family:"Oswald",sans-serif;font-weight:300;font-size:11px;display:flex;align-items:center;justify-content:center;gap:5px;color:var(--ink)}
.logo{position:absolute;left:0;right:0;top:47px;text-align:center;font-family:"Oswald",sans-serif;font-weight:400;font-size:28px;line-height:40px;letter-spacing:5px;color:var(--ink)}
.main-nav{left:0;right:0;top:145px;height:52px;border-top:1px solid var(--frame)}
.main-nav a{position:absolute;top:16px;font-family:"Oswald",sans-serif;font-weight:300;font-size:13px;color:var(--ink);text-decoration:none}
.main-nav a.is-active{font-weight:500}
.cart-total{position:absolute;left:801px;top:12px;font-family:"Oswald",sans-serif;font-weight:300;font-size:12px;line-height:16px;color:var(--red)}
.nav-divider{position:absolute;left:850px;top:0;width:1px;height:51px;background:var(--frame)}

/* hero */
.hero{left:132px;top:267px;width:934px;height:561px;background:var(--navy);overflow:hidden}
.hero__band{position:absolute;left:0;width:100%}
.hero__photo{position:absolute;left:43px;top:25px;width:387px;height:536px;background:linear-gradient(160deg,#3a2a2c,#6b4a44 55%,#1d1d22)}
.hero__eyebrow{left:465px;top:211px;font-family:"Oswald",sans-serif;font-size:13px;color:var(--red)}
.hero__title{left:463px;top:228px;font-family:"Oswald",sans-serif;font-weight:400;font-size:38px;color:var(--ink);letter-spacing:-.3px}
.hero__art{left:460px;top:290px;width:120px;height:135px;background:rgba(255,255,255,.22)}
.hero__sub{left:620px;top:365px;font-family:"Oswald",sans-serif;font-weight:300;font-size:22px;line-height:26px;color:var(--ink)}
.hero__dots{left:472px;top:519px;display:flex;gap:9px}
.hero__dots span{width:9px;height:9px;border-radius:50%;background:var(--white)}
.hero__dots span.is-current{background:var(--band-red)}
.slider-arrow{top:455px}

/* promos */
.promo{top:866px;width:447px;height:121px;border:1px solid var(--muted)}
.promo__inner{position:absolute;inset:9px;border:1px solid var(--frame);text-align:center;padding-top:22px}
.promo__title{font-family:"Oswald",sans-serif;font-size:24px;color:var(--red)}
.promo__note{font-family:"Oswald",sans-serif;font-weight:300;font-size:11px;color:var(--red)}

/* section heads */
.section-rule{left:132px;width:934px;height:1px;background:var(--muted)}
.section-rule::before{content:"";position:absolute;left:0;top:-1px;width:110px;height:2px;background:var(--muted)}
.section-title{left:132px;font-family:"Oswald",sans-serif;font-weight:300;font-size:21px;color:var(--ink)}
.pager{width:33px;height:33px;border:1px solid var(--muted);display:flex;align-items:center;justify-content:center}

/* products */
.product{top:1107px;width:229px;height:293px}
.product__photo{width:229px;height:196px}
.product__info{height:69px;border:1px solid var(--line);border-top:none;text-align:center}
.product__name{font-family:"Oswald",sans-serif;font-weight:300;font-size:14px;padding-top:13px;color:var(--ink)}
.product__price{font-family:"Oswald",sans-serif;font-weight:300;font-size:14px;margin-top:5px;color:var(--ink)}
.product__actions{display:flex;height:29px;border:1px solid var(--line)}
.product__actions span{flex:1;display:flex;align-items:center;justify-content:center;gap:6px;font-size:10px;color:var(--muted);text-transform:uppercase}
.product__actions span+span{border-left:1px solid var(--line)}

/* news */
.news{top:1508px;width:300px;height:96px}
.news__photo{position:absolute;left:0;top:2px;width:115px;height:92px}
.news__body{position:absolute;left:131px;top:0;width:165px}
.news__title{font-family:"Oswald",sans-serif;font-weight:300;font-size:14px;color:var(--ink)}
.news__meta{font-size:9px;color:var(--ink);margin-top:4px;text-transform:uppercase}
.news__text{font-size:11px;line-height:16px;color:var(--muted);margin-top:6px;height:48px;overflow:hidden}

/* footer columns */
.col-title{top:1645px;width:213px;font-family:"Oswald",sans-serif;font-weight:300;font-size:21px;color:var(--ink);border-bottom:1px solid var(--muted);padding-bottom:2px}
.about__mark{left:132px;top:1690px;width:70px;height:73px;background:#dddddd}
.about__text{left:211px;top:1681px;width:150px;font-size:13px;line-height:22px;color:var(--ink)}
.about__line{left:132px;font-size:12px;line-height:16px;color:var(--ink)}
.mini{width:213px;height:110px}
.mini__photo{position:absolute;left:0;top:0;width:79px;height:109px}
.mini__name{position:absolute;left:92px;top:2px;font-family:"Oswald",sans-serif;font-weight:300;font-size:13px;color:var(--ink)}
.mini__stars{position:absolute;left:92px;top:25px}
.mini__price{position:absolute;left:92px;top:48px;font-family:"Oswald",sans-serif;font-weight:400;font-size:19px;color:var(--ink)}
.mini-rule{width:213px;height:1px;background:var(--line)}
.tags{left:832px;top:1713px;width:240px;display:flex;flex-wrap:wrap;gap:7px 8px}
.tag{height:34px;padding:0 15px;border:1px solid var(--line);display:flex;align-items:center;font-size:13px;color:var(--ink)}
.tag.is-active{background:var(--tag-red);border-color:var(--tag-red);color:var(--white)}
.social{left:832px;top:1899px;display:flex;gap:6px}
.social span{width:34px;height:34px;border:1px solid var(--line)}
.policy-link{left:832px;width:213px;font-family:"Oswald",sans-serif;font-weight:300;font-size:12px;color:var(--ink);display:flex;justify-content:space-between;align-items:center}
.policy-rule{left:832px;width:213px;height:1px;background:var(--line)}

/* footer bar */
.site-footer{left:132px;top:2165px;width:934px;height:57px;border:2px solid var(--ink)}
.site-footer__text{position:absolute;left:18px;top:18px;font-family:"Oswald",sans-serif;font-weight:300;font-size:12px;color:var(--ink)}
.payments{position:absolute;right:12px;top:16px;display:flex;gap:4px}
.payments span{width:33px;height:21px;border-radius:2px;background:#dddddd}
.payments span:nth-child(2n){background:#aaaaaa}
</style>
</head>
<body>

<header class="site-header abs">
  <div class="site-header__inner">
    <p class="contact-line abs" style="top:25px">41 LARKSPUR AVE CHICAGO, IL 60614</p>
    <p class="contact-line abs" style="top:51px">CONTACT@QUILLMOSS.COM</p>
    <div class="account-btn abs">
      <svg width="8" height="6" viewBox="0 0 8 6"><path d="M1 1l3 3 3-3" fill="none" stroke="#1b1b1b" stroke-width="1.3"/></svg>
      MY ACCOUNT
    </div>
    <div class="logo">TRESSES BY JOLAVIE</div>
    <nav class="main-nav abs">
      <a class="is-active" style="left:31px">HOME</a>
      <a style="left:99px">THEME FEATURES</a>
      <a style="left:221px">SHOP</a>
      <a style="left:286px">PORTFOLIO</a>
      <a style="left:378px">THE BLOG</a>
      <a style="left:464px">BUY THEME</a>
      <svg class="abs" style="left:766px;top:12px" width="24" height="30" viewBox="0 0 24 30"><path d="M3 8h18l-1 20H4z" fill="#f2f2f2" stroke="#aaaaaa"/><path d="M8 8V5a4 4 0 0 1 8 0v3" fill="none" stroke="#aaaaaa"/></svg>
      <div class="cart-total">$0.00<br>0 ITEMS</div>
      <span class="nav-divider"></span>
      <svg class="abs" style="left:884px;top:16px" width="20" height="20" viewBox="0 0 20 20"><circle cx="8" cy="8" r="6" fill="none" stroke="#1b1b1b" stroke-width="1.5"/><path d="M12.5 12.5l6 6" stroke="#1b1b1b" stroke-width="1.8"/></svg>
    </nav>
  </div>
</header>

<svg class="slider-arrow abs" style="left:61px" width="24" height="46" viewBox="0 0 24 46"><path d="M22 2L2 23l20 21" fill="none" stroke="#aaaaaa" stroke-width="2"/></svg>
<svg class="slider-arrow abs" style="left:1102px" width="24" height="46" viewBox="0 0 24 46"><path d="M2 2l20 21L2 44" fill="none" stroke="#aaaaaa" stroke-width="2"/></svg>

<section class="hero abs">
  <div class="hero__band" style="top:0;height:189px;background:linear-gradient(110deg,#2c5670 0%,#1d2c38 55%)"></div>
  <div class="hero__band" style="top:189px;height:95px;background:var(--band-grey)"></div>
  <div class="hero__band" style="top:284px;height:67px;background:var(--band-red)"></div>
  <div class="hero__band" style="top:351px;height:96px;background:var(--band-grey)"></div>
  <div class="hero__photo" role="img" aria-label="Smiling model with long wavy dark hair extensions"></div>
  <p class="hero__eyebrow abs">WE SELL 100% HUMAN HAIR IN BRAZILIAN BODY WAVE DEEP WAVE</p>
  <h1 class="hero__title abs">STRAIGHT OR NATURAL CURL.</h1>
  <div class="hero__art abs" role="img" aria-label="Outline illustration of shopping bags"></div>
  <p class="hero__sub abs">HARBOR CORVALEN TEAM<br>IS MOVING OFFICES</p>
  <div class="hero__dots abs"><span></span><span class="is-current"></span><span></span></div>
</section>

<div class="promo abs" style="left:132px"><div class="promo__inner"><p class="promo__title">GET 25% OFF WHEN YOU SPEND $100</p><p class="promo__note">LIMITED TIME ONLY | USE CODE: QUILLMOSS</p></div></div>
<div class="promo abs" style="left:620px"><div class="promo__inner"><p class="promo__title">GET 25% OFF WHEN YOU SPEND $100</p><p class="promo__note">LIMITED TIME ONLY | USE CODE: QUILLMOSS</p></div></div>

<!-- best sellers -->
<div class="section-rule abs" style="top:1039px"></div>
<h2 class="section-title abs" style="top:1052px">BEST SELLERS</h2>
<div class="pager abs" style="left:998px;top:1039px"><svg width="8" height="12" viewBox="0 0 8 12"><path d="M6 1L1 6l5 5" fill="none" stroke="#1b1b1b" stroke-width="1.6"/></svg></div>
<div class="pager abs" style="left:1033px;top:1039px"><svg width="8" height="12" viewBox="0 0 8 12"><path d="M2 1l5 5-5 5" fill="none" stroke="#1b1b1b" stroke-width="1.6"/></svg></div>

<article class="product abs" style="left:132px">
  <div class="product__photo" role="img" aria-label="Customer wearing curly hair extensions" style="background:linear-gradient(150deg,#3c4a2c,#5a4a66 60%,#3b4fa8)"></div>
  <div class="product__info"><p class="product__name">Harbor AdipiscingCorvalen</p><p class="product__price">$100.00</p></div>
  <div class="product__actions"><span>♡ Wishlist</span><span>⇄ Compare</span></div>
</article>
<article class="product abs" style="left:368px">
  <div class="product__photo" role="img" aria-label="Customer wearing long box braids" style="background:linear-gradient(150deg,#e6c8cf,#b8866c 55%,#e9d3d8)"></div>
  <div class="product__info"><p class="product__name">Harbor AdipiscingCorvalen</p><p class="product__price">$100.00</p></div>
  <div class="product__actions"><span>♡ Wishlist</span><span>⇄ Compare</span></div>
</article>
<article class="product abs" style="left:604px">
  <div class="product__photo" role="img" aria-label="Two customers showing straight hair extensions" style="background:linear-gradient(150deg,#6a5446,#3a2520 55%,#8c6a52)"></div>
  <div class="product__info"><p class="product__name">Harbor AdipiscingCorvalen</p><p class="product__price">$100.00</p></div>
  <div class="product__actions"><span>♡ Wishlist</span><span>⇄ Compare</span></div>
</article>
<article class="product abs" style="left:840px">
  <div class="product__photo" role="img" aria-label="Back view of deep wave hair extensions" style="background:linear-gradient(150deg,#b49a72,#2b3f7c 50%,#1a2a5a)"></div>
  <div class="product__info"><p class="product__name">Harbor AdipiscingCorvalen</p><p class="product__price">$100.00</p></div>
  <div class="product__actions"><span>♡ Wishlist</span><span>⇄ Compare</span></div>
</article>

<!-- latest news -->
<div class="section-rule abs" style="top:1440px"></div>
<h2 class="section-title abs" style="top:1453px">LATEST NEWS</h2>
<div class="pager abs" style="left:998px;top:1440px"><svg width="8" height="12" viewBox="0 0 8 12"><path d="M6 1L1 6l5 5" fill="none" stroke="#1b1b1b" stroke-width="1.6"/></svg></div>
<div class="pager abs" style="left:1033px;top:1440px"><svg width="8" height="12" viewBox="0 0 8 12"><path d="M2 1l5 5-5 5" fill="none" stroke="#1b1b1b" stroke-width="1.6"/></svg></div>

<article class="news abs" style="left:132px">
  <div class="news__photo" role="img" aria-label="Tablet on a bright green desk" style="background:linear-gradient(135deg,#1e2a14,#b9e23a 70%)"></div>
  <div class="news__body"><h3 class="news__title">Corvalen Visits Their New Office</h3><p class="news__meta">0 Comments</p><p class="news__text">The Harbor Corvalen team is moving offices in July. We took the team to check out the new</p></div>
</article>
<article class="news abs" style="left:445px">
  <div class="news__photo" role="img" aria-label="Lit server room corridor" style="background:linear-gradient(90deg,#121a2e,#4a6a9c 50%,#121a2e)"></div>
  <div class="news__body"><h3 class="news__title">Corvalen Visits Their New Office</h3><p class="news__meta">0 Comments</p><p class="news__text">The Harbor Corvalen team is moving offices in July. We took the team to check out the new</p></div>
</article>
<article class="news abs" style="left:756px">
  <div class="news__photo" role="img" aria-label="Team working at computers in an office" style="background:linear-gradient(135deg,#6e8a5a,#d9d6cc 55%,#8a4a3a)"></div>
  <div class="news__body"><h3 class="news__title">Corvalen Visits Their New Office</h3><p class="news__meta">0 Comments</p><p class="news__text">The Harbor Corvalen team is moving offices in July. We took the team to check out the new</p></div>
</article>

<!-- footer columns -->
<h2 class="col-title abs" style="left:132px">ABOUT US</h2>
<div class="about__mark abs"></div>
<p class="about__text abs">Lorem ipsum dolor<br>sit amet, consectetur<br>adipiscing elit. Quis<br>que porta.</p>
<p class="about__line abs" style="top:1780px">t: 1-800-555-0142</p>
<p class="about__line abs" style="top:1802px">f: 1-800-555-0143</p>
<p class="about__line abs" style="top:1824px">e: contact@quillmoss.com</p>

<svg width="0" height="0" style="position:absolute"><defs><path id="star" d="M5 0l1.5 3.3 3.5.4-2.6 2.4.7 3.5L5 7.8 1.9 9.6l.7-3.5L0 3.7l3.5-.4z"/></defs></svg>

<h2 class="col-title abs" style="left:365px">TOP RATED PRODUCTS</h2>
<div class="mini abs" style="left:365px;top:1713px"><div class="mini__photo" role="img" aria-label="Customer with long straight hair" style="background:linear-gradient(160deg,#8a8fa0,#3d3040 60%,#5a6ab0)"></div><p class="mini__name">Text Trim Fit Blazer</p><svg class="mini__stars" width="60" height="10" viewBox="0 0 60 10"><g fill="#9e1b20"><use href="#star"/><use href="#star" x="12"/><use href="#star" x="24"/><use href="#star" x="36"/></g><use href="#star" x="48" fill="#606060"/></svg><p class="mini__price">$175.00</p></div>
<div class="mini-rule abs" style="left:365px;top:1838px"></div>
<div class="mini abs" style="left:365px;top:1853px"><div class="mini__photo" role="img" aria-label="Customer with curly hair extensions" style="background:linear-gradient(160deg,#c8b8a8,#2a2426 55%,#4a5aa0)"></div><p class="mini__name">Text Trim Fit Blazer</p><svg class="mini__stars" width="60" height="10" viewBox="0 0 60 10"><g fill="#9e1b20"><use href="#star"/><use href="#star" x="12"/><use href="#star" x="24"/><use href="#star" x="36"/></g><use href="#star" x="48" fill="#606060"/></svg><p class="mini__price">$175.00</p></div>
<div class="mini-rule abs" style="left:365px;top:1975px"></div>
<div class="mini abs" style="left:365px;top:1990px"><div class="mini__photo" role="img" aria-label="Child with braided hairstyle" style="background:linear-gradient(160deg,#d8d0c8,#5a3a30 55%,#c8a0b8)"></div><p class="mini__name">Text Trim Fit Blazer</p><svg class="mini__stars" width="60" height="10" viewBox="0 0 60 10"><g fill="#9e1b20"><use href="#star"/><use href="#star" x="12"/><use href="#star" x="24"/><use href="#star" x="36"/></g><use href="#star" x="48" fill="#606060"/></svg><p class="mini__price">$175.00</p></div>

<h2 class="col-title abs" style="left:598px">ON SALE</h2>
<div class="mini abs" style="left:598px;top:1713px"><div class="mini__photo" role="img" aria-label="Customer in green top with short hairstyle" style="background:linear-gradient(160deg,#d8d8d0,#4a3a34 45%,#4a9a4a)"></div><p class="mini__name">Text Trim Fit Blazer</p><svg class="mini__stars" width="60" height="10" viewBox="0 0 60 10"><g fill="#9e1b20"><use href="#star"/><use href="#star" x="12"/><use href="#star" x="24"/><use href="#star" x="36"/></g><use href="#star" x="48" fill="#606060"/></svg><p class="mini__price">$175.00</p></div>
<div class="mini-rule abs" style="left:598px;top:1838px"></div>
<div class="mini abs" style="left:598px;top:1853px"><div class="mini__photo" role="img" aria-label="Child with styled puffs" style="background:linear-gradient(160deg,#c8a890,#5a3a30 50%,#d87a6a)"></div><p class="mini__name">Text Trim Fit Blazer</p><svg class="mini__stars" width="60" height="10" viewBox="0 0 60 10"><g fill="#9e1b20"><use href="#star"/><use href="#star" x="12"/><use href="#star" x="24"/><use href="#star" x="36"/></g><use href="#star" x="48" fill="#606060"/></svg><p class="mini__price">$175.00</p></div>
<div class="mini-rule abs" style="left:598px;top:1975px"></div>
<div class="mini abs" style="left:598px;top:1990px"><div class="mini__photo" role="img" aria-label="Customer with straight shoulder-length hair" style="background:linear-gradient(160deg,#d0d0d8,#2a2428 50%,#4a5aa0)"></div><p class="mini__name">Text Trim Fit Blazer</p><svg class="mini__stars" width="60" height="10" viewBox="0 0 60 10"><g fill="#9e1b20"><use href="#star"/><use href="#star" x="12"/><use href="#star" x="24"/><use href="#star" x="36"/></g><use href="#star" x="48" fill="#606060"/></svg><p class="mini__price">$175.00</p></div>

<h2 class="col-title abs" style="left:832px">PRODUCT TAGS</h2>
<div class="tags abs">
  <span class="tag is-active">Black</span><span class="tag">Classic</span><span class="tag">Men</span>
  <span class="tag">Polo Shirts</span><span class="tag">Sale</span><span class="tag">Suit</span>
  <span class="tag">Summer</span>
</div>
<h2 class="col-title abs" style="left:832px;top:1842px">QUILLMOSS SOCIAL</h2>
<div class="social abs"><span></span><span></span><span></span><span></span><span></span></div>
<p class="policy-link abs" style="top:1963px">Terms and Conditions <svg width="6" height="10" viewBox="0 0 6 10"><path d="M1 1l4 4-4 4" fill="none" stroke="#1b1b1b"/></svg></p>
<div class="policy-rule abs" style="top:1990px"></div>
<p class="policy-link abs" style="top:2003px">Retrn Policy <svg width="6" height="10" viewBox="0 0 6 10"><path d="M1 1l4 4-4 4" fill="none" stroke="#1b1b1b"/></svg></p>

<footer class="site-footer abs">
  <p class="site-footer__text">Tresses by Jolavie © 2014 • Privacy Policy</p>
  <div class="payments" aria-label="Accepted payment methods"><span></span><span></span><span></span><span></span><span></span><span></span><span></span><span></span><span></span><span></span><span></span></div>
</footer>

</body>
</html>
```